Flyer-Design für bildenden Künstler
Zielgruppe
Ich bin bildender Künstler, benötige einen außergewöhnlichen, sehr ästhetischen, einzigartigen, als Eyecatcher fungierenden, meine Kunst und Identität repräsentierenden Flyer zum Auslegen, um neue KundInnen zu gewinnen.
Aufgabenstellung
Er soll wenig Text beinhalten (ein Zitat, Anschrift und Kontaktmöglichkeiten, ein kleines statement zu meiner Kunstphilosophie), und Bilder meiner Kunst zeigen. Raum ist mir wichtig, genug Leerräume, damit ein in Szene gesetztes Zitat oder Foto meiner Kunstwerke gut wirken kann. Es soll Lust darauf machen, Anreiz bieten und Interesse wecken, auf meine homepage zu gehen. Die Einzigartigkeit meiner Kunst soll deutlich werden.
Die hochgelandenen Fotos zeigen meine Kunstwerke. Sie können als Hintergrundbild fungieren und dementsprechend auch die ganze Seite ausfüllen, sie können zugeschnitten werden und/oder mit Text überlagert sein. Manche Fotos (zum Beispiel die Kunstwerke mit Rahmen) eignen sich dagegen, sie auf einer ganzen Seite zu zeigen, ohne einen Text dazu. So eine Seite würde ich jedenfalls gerne dabei haben, wo ein Kunstwerk für sich alleine auf einer ganzen Seite dargestellt wird. 1O4A2598 oder 1O4A6076a bieten sich dafür an (diese und alle anderen Fotos sind zum Teil komprimiert und zugeschnitten; falls gewünscht bzw. die Qualität nicht gut ist, kann ich das Originalfoto senden, das unkomprimiert und nicht zugeschnitten ist. Auch kann die Helligkeit oder die Farbqualität verbessert werden, falls notwendig). Nicht alle Kunstbilder müssen verwendet werden.
Ich bin offen für jedes Flyerformat, tendiere zu einem ein 2 oder 3-seitigen Falzflyer hochkant oder im Querformat. Bin aber offen für Ideen und Vorschläge.
Die Texte unter der Datei 'Texte, Adresse, Zitate' enthalten einen kleinen Text, der verwendet werden soll. Unter 'Text für die Titelseite' ist ein Vorschlag für die Titelseite zu finden. Die Adresse muss vollständig erscheinen, und unter 'Zitate' sind mehrere meiner Zitate - auch davon soll eines verwendet werden.
BITTE AUSSCHLIEßLICH DIE FOTOS UND TEXTE VERWENDEN, DIE ICH HOCHGELADEN HABE, UND NICHTS VON MEINEN HOMEPAGES NEHMEN. DANKE!

```html
<!DOCTYPE html>
<html lang="de">
<head>
<meta charset="utf-8">
<title>Lukas Brandner Art – Falzflyer</title>
<link href="https://fonts.googleapis.com/css2?family=Montserrat:wght@400;500;700;800&display=swap" rel="stylesheet">
<style>
  :root {
    --bg: #e9edf0;
    --slate: #6e8ea3;
    --title-blue: #4f7891;
    --paper-white: #f7f7f7;
    --paper-light: #ececec;
    --paper-grey: #c9c9c9;
    --teal: #2f8fae;
    --teal-dark: #1c4f63;
    --frame: #8d8f91;
    --ink-soft: #5a6f7c;
    --white: #ffffff;
  }
  * { box-sizing: border-box; margin: 0; padding: 0; }
  html, body {
    width: 1200px; height: 900px; overflow: hidden;
    background: var(--bg);
    font-family: "Montserrat", sans-serif;
  }
  .stage {
    position: relative; width: 1200px; height: 900px;
    display: flex; justify-content: center; align-items: center; gap: 34px;
  }
  .spread {
    display: flex; width: 558px; height: 414px;
    box-shadow: 0 10px 30px rgba(40, 60, 75, 0.18);
  }
  .panel {
    position: relative; width: 186px; height: 414px;
    display: flex; flex-direction: column; align-items: center;
  }
  .panel--slate { background: var(--slate); justify-content: center; padding: 0 14px; }
  .panel--light { background: linear-gradient(90deg, var(--paper-white), var(--paper-light)); }
  .panel--grey { background: linear-gradient(90deg, #d6d6d6, var(--paper-grey)); }
  .panel--white { background: var(--paper-white); }

  .quote-mark {
    color: var(--white); font-weight: 800; font-size: 44px; line-height: 1;
    height: 30px; margin-bottom: 14px;
  }
  .quote-text {
    color: var(--white); font-weight: 700; font-size: 10.5px; line-height: 1.75;
    text-align: center;
  }

  .contact {
    position: absolute; bottom: 22px; left: 0; right: 0;
    text-align: center; color: var(--ink-soft); font-size: 8.4px; line-height: 1.3;
  }
  .contact__name { font-weight: 700; }
  .contact__block + .contact__block { margin-top: 12px; }
  .contact__web { font-weight: 700; }

  .cover-title {
    margin-top: 36px; text-align: center; color: var(--title-blue);
    font-weight: 800; font-size: 19px; line-height: 1.2;
  }
  .cover-subtitle {
    margin-top: 4px; text-align: center; color: var(--title-blue);
    font-weight: 700; font-size: 12px;
  }
  .dash { width: 22px; height: 3px; background: var(--title-blue); margin-top: 12px; }

  .art-circle {
    width: 138px; height: 138px; border-radius: 50%; margin-top: 38px;
    background: radial-gradient(circle at 40% 40%, var(--teal), var(--teal-dark));
  }

  .brand {
    position: absolute; bottom: 22px; left: 0; right: 0;
    display: flex; justify-content: center; align-items: center; gap: 6px;
    color: #3a3a3a; font-weight: 500; font-size: 13px; letter-spacing: 0.5px;
  }
  .brand__square { width: 8px; height: 8px; background: #b8a58a; }

  .framed-art {
    position: absolute; top: 30px; bottom: 30px; left: 28px; right: 28px;
    border: 5px solid var(--frame); background: var(--frame);
  }
  .framed-art__image {
    width: 100%; height: 100%;
    background: radial-gradient(ellipse at 50% 45%, var(--teal), var(--teal-dark));
  }

  .philosophy { align-items: flex-start; padding: 46px 20px 0 30px; }
  .philosophy__title {
    color: var(--title-blue); font-weight: 800; font-size: 18px; line-height: 1.25;
  }
  .philosophy .dash { margin-top: 16px; }
  .philosophy__text {
    margin-top: 24px; color: var(--title-blue); font-size: 8.6px; line-height: 1.6;
  }
</style>
</head>
<body>
<main class="stage">

  <section class="spread spread--outside" aria-label="Außenseite">
    <div class="panel panel--slate">
      <div class="quote-mark">“</div>
      <p class="quote-text">Kunst unterstreicht Deinen guten Geschmack. Es zeugt davon, dass Du Weitblick besitzt. Und offen für neue Erfahrungen bist.</p>
    </div>
    <div class="panel panel--light">
      <div class="contact">
        <div class="contact__block">
          <div class="contact__name">Lukas Brandner</div>
          <div>Am Lindengarten 7</div>
          <div>79102 Talheim</div>
        </div>
        <div class="contact__block">
          <div>(+49) 0761 5550 1827</div>
          <div>brandner-art@mailpost.de</div>
        </div>
        <div class="contact__block contact__web">www.brandner-art.de</div>
      </div>
    </div>
    <div class="panel panel--grey">
      <h1 class="cover-title">Lukas<br>Brandner Art</h1>
      <div class="cover-subtitle">Transformationen</div>
      <div class="dash"></div>
      <div class="art-circle" role="img" aria-label="Ausschnitt eines Kunstwerks aus türkisblauem, porösem Material"></div>
      <div class="brand"><span class="brand__square"></span>Brandner Art</div>
    </div>
  </section>

  <section class="spread spread--inside" aria-label="Innenseite">
    <div class="panel panel--grey">
      <div class="framed-art">
        <div class="framed-art__image" role="img" aria-label="Gerahmtes Kunstwerk aus dunklem türkisblauem, porösem Material"></div>
      </div>
    </div>
    <div class="panel panel--light philosophy">
      <h2 class="philosophy__title">The<br>Philosophy</h2>
      <div class="dash"></div>
      <p class="philosophy__text">Seit jeher fasziniert mich die Transformation eines Zustandes in einen anderen. Das ganze Leben ist eine fortwährende Veränderung, nichts bleibt, wie es ist. Ich setze mich damit auseinander und gebe Material und Vergangenem eine neue Sinnhaftigkeit.</p>
      <div class="brand"><span class="brand__square"></span>Brandner Art</div>
    </div>
    <div class="panel panel--white">
      <div class="framed-art">
        <div class="framed-art__image" role="img" aria-label="Gerahmtes Kunstwerk aus hellem türkisblauem, porösem Material"></div>
      </div>
    </div>
  </section>

</main>
</body>
</html>
```